Packaging Design: Logo/Bottle Design for New Botanical Cocktail Brand

We are a new start up, looking to create a new line of Ready to drink Cocktails. The brand name is Verdance Garden Spritzers, infused with fruit, herb, and floral botanicals grown on our farm in New Hampshire. Flavors will include: Herb flavored with cilantro, Berry- flavored with Ridgeglow Berry, Citrus flavored with lemon Verbena & lemon balm, Pear flavored with Quillon pear, Cucumber & Mint. We need a logo and a label design. There are 2 possible bottles to choose from.

Designer has complete freedom with everything! From fonts and colors to bottle caps and closures. Please view the pinterest link for inspirational bottle designs. https://www.pinboardia.com/dellacravitz/garden-spritzers/

Reason: I am extending the deadline for my project to allow more designers to submit their designs.

Target Market(s)

Female 21 to 48 years old. College educated and professional. The type of person that has a passion for a cause and eats and shops local. People that respect an artisan quality product, hand made by a master craftsman.

Industry/Entity Type

Floral

Requirements
Must have
• Clear Bottle, see options attached. You may also choose your own BUT WE MUST SEE THE LOGO AND IMAGERY ON A BOTTLE
• Logo Design: "Verdance Garden Spritzers"
• Label: We can have front and back, or one continuous label. We are open to painted designs.
• The label must contain the following text in quotes:
• Product Name: " Verdance Garden Spritzers "
• "15% Alc. by Vol. (30 proof)"
• "750 mL"
• "Handcrafted and Bottled by Hollowmere Stillbrook Farm and Distillery
• Winchester, NH-USA"
• The following Text must be in all caps and 3mm in height:
• "Government Warning: (1) According to the Surgeon General, women should not drink alcoholic beverages during pregnancy because of the risk of birth defects. (2) Consumption of alcoholic beverages impairs your ability to drive a car or operate machinery and may cause health problems."
• Must be a space for a bar code: .75 in height by 1.25 in length.
• “www.hollowmerestillbrook.com”
• Must Have the following Statement:
• Infused with fruit, herb, and floral botanicals and sweetened with stevia. Serve cold over ice.
Nice to have
• Antique or vintage botanical illustrations
• https://www.pinboardia.com/dellacravitz/garden-spritzers/
• check out the board for inspiration.
• Think artisanal small batch spirits that are ready to drink out of the bottle. Refreshing flavors just pour over ice and add herb leaves.
• You can use images by doing a search here.
• http://archv.plantrec.example.org/archv/search.xhtml?start=0&collectionFacet=Orchard+Painted+Plate+Archive

```html
<!DOCTYPE html>
<html lang="en">
<head>
<meta charset="utf-8">
<title>Verdance Garden Spritzers — Bottle Range</title>
<link rel="stylesheet" href="https://fonts.googleapis.com/css2?family=Josefin+Sans:wght@300;400&family=Cormorant+Garamond:wght@500&display=swap">
<style>
  :root {
    --bg-top: #d8f5f4;
    --bg-mid: #5f9193;
    --bg-bottom: #12211f;
    --glass: rgba(235, 242, 244, 0.55);
    --glass-edge: rgba(255, 255, 255, 0.35);
    --cap: #2b2e2d;
    --neck-dark: #33352c;
    --neck-tan: #efc996;
    --rose-gold: #c48f7a;
    --rose-berry: #c57b8c;
    --label-white: #ffffff;
    --band: rgba(215, 222, 222, 0.55);
    --band-light: rgba(225, 230, 230, 0.7);
    --ink: #2a2d2c;
    --copper: #c9a07d;
    --pear: #c8b56a;
    --citrus: #d69a4a;
    --berry: #d9574f;
  }
  * { margin: 0; padding: 0; box-sizing: border-box; }
  html, body { width: 1200px; height: 1200px; overflow: hidden; }
  body {
    position: relative;
    background: linear-gradient(180deg, var(--bg-top) 0%, var(--bg-mid) 45%, #2d5458 72%, var(--bg-bottom) 100%);
    font-family: "Josefin Sans", sans-serif;
  }
  .bottle { position: absolute; top: 33px; width: 169px; height: 1100px; }
  .bottle svg { position: absolute; inset: 0; }
  .neck-mark {
    position: absolute; top: 215px; left: 0; width: 169px;
    text-align: center;
    font-family: "Cormorant Garamond", serif; font-weight: 500;
    font-size: 19px; color: var(--rose-gold);
  }
  .neck-mark.berry { color: var(--rose-berry); }

  /* white front label */
  .label-white {
    position: absolute; left: 14px; top: 384px; width: 131px; height: 447px;
    background: var(--label-white);
    text-align: center;
  }
  .seal {
    position: absolute; left: 1px; top: 5px; width: 130px; height: 130px;
    border-radius: 50%;
    background: radial-gradient(circle at 40% 35%, #d9b89a, #a87e6c);
    display: flex; align-items: center; justify-content: center;
    font-family: "Cormorant Garamond", serif; font-weight: 500;
    font-size: 21px; color: #fbeee2;
  }
  .label-white .fruit { position: absolute; left: 4px; top: 137px; width: 124px; height: 134px; }
  .label-white .brand {
    position: absolute; top: 290px; width: 100%;
    font-weight: 300; font-size: 17px; line-height: 27px;
    color: var(--copper); letter-spacing: 0.3px;
  }
  .label-white .flavor {
    position: absolute; top: 397px; width: 100%;
    font-weight: 300; font-size: 21px; color: var(--ink); letter-spacing: 1px;
  }

  /* clear band label */
  .label-clear { position: absolute; left: 0; top: 410px; width: 169px; height: 405px; }
  .label-clear .tier {
    position: absolute; left: 0; width: 100%;
    border-top: 1px solid rgba(60, 70, 72, 0.6);
  }
  .tier.top { top: 0; height: 132px; background: var(--band-light); }
  .tier.mid { top: 132px; height: 142px; background: rgba(160, 180, 182, 0.25); }
  .tier.low { top: 274px; height: 131px; background: var(--band); border-bottom: 1px solid rgba(60, 70, 72, 0.6); }
  .label-clear .flavor {
    position: absolute; top: 9px; width: 100%; text-align: center;
    font-size: 16px; font-weight: 400; letter-spacing: 3.5px; color: var(--ink);
  }
  .label-clear .fruit { position: absolute; left: 25px; top: 33px; width: 120px; height: 138px; }
  .label-clear .mark {
    position: absolute; top: 205px; width: 100%; text-align: center;
    font-family: "Cormorant Garamond", serif; font-weight: 500;
    font-size: 28px; color: var(--rose-gold);
  }
  .label-clear .mark.berry { color: var(--rose-berry); }
  .label-clear .brand {
    position: absolute; top: 292px; width: 100%; text-align: center;
    font-weight: 300; font-size: 23px; line-height: 33px;
    color: #f4f6f6; letter-spacing: 0.5px;
  }
</style>
</head>
<body>

<svg width="0" height="0" style="position:absolute">
  <defs>
    <linearGradient id="glass-shade" x1="0" x2="1">
      <stop offset="0" stop-color="#e6eef0" stop-opacity="0.55"/>
      <stop offset="0.2" stop-color="#ffffff" stop-opacity="0.35"/>
      <stop offset="0.5" stop-color="#e6eef0" stop-opacity="0.15"/>
      <stop offset="0.8" stop-color="#ffffff" stop-opacity="0.35"/>
      <stop offset="1" stop-color="#e6eef0" stop-opacity="0.55"/>
    </linearGradient>
  </defs>
</svg>

<!-- Bottle 1: white label, pear -->
<div class="bottle" style="left:148px">
  <svg viewBox="0 0 169 1100" aria-hidden="true">
    <path d="M37 0 H132 V300 C132 330 169 340 169 380 V1085 Q169 1100 154 1100 H15 Q0 1100 0 1085 V380 C0 340 37 330 37 300 Z" fill="url(#glass-shade)" stroke="var(--glass-edge)" stroke-width="2"/>
    <rect x="37" y="0" width="95" height="146" rx="5" fill="var(--cap)"/>
    <rect x="37" y="146" width="95" height="154" fill="var(--neck-tan)"/>
    <ellipse cx="84.5" cy="1035" rx="78" ry="18" fill="#ffffff" fill-opacity="0.2"/>
  </svg>
  <div class="neck-mark">Verdance</div>
  <div class="label-white">
    <div class="seal">Verdance</div>
    <svg class="fruit" role="img" aria-label="Vintage botanical illustration of a pear with leaves" viewBox="0 0 124 134">
      <rect width="124" height="134" fill="var(--pear)" opacity="0.55" rx="10"/>
    </svg>
    <div class="brand">VERDANCE<br>GARDEN<br>SPRITZERS</div>
    <div class="flavor">PEAR</div>
  </div>
</div>

<!-- Bottles 2–4: clear band labels -->
<div class="bottle" style="left:450px">
  <svg viewBox="0 0 169 1100" aria-hidden="true">
    <path d="M37 0 H132 V300 C132 330 169 340 169 380 V1085 Q169 1100 154 1100 H15 Q0 1100 0 1085 V380 C0 340 37 330 37 300 Z" fill="url(#glass-shade)" stroke="var(--glass-edge)" stroke-width="2"/>
    <rect x="37" y="0" width="95" height="146" rx="5" fill="var(--cap)"/>
    <rect x="37" y="143" width="95" height="160" fill="var(--neck-dark)"/>
    <ellipse cx="84.5" cy="1035" rx="78" ry="18" fill="#ffffff" fill-opacity="0.2"/>
  </svg>
  <div class="neck-mark">Verdance</div>
  <div class="label-clear">
    <div class="tier top"></div><div class="tier mid"></div><div class="tier low"></div>
    <div class="flavor">CITRUS</div>
    <svg class="fruit" role="img" aria-label="Vintage botanical illustration of lemon and orange on a leafy branch" viewBox="0 0 120 138">
      <rect width="120" height="138" fill="var(--citrus)" opacity="0.5" rx="10"/>
    </svg>
    <div class="mark">Verdance</div>
    <div class="brand">VERDANCE<br>GARDEN<br>SPRITZERS</div>
  </div>
</div>

<div class="bottle" style="left:659px">
  <svg viewBox="0 0 169 1100" aria-hidden="true">
    <path d="M37 0 H132 V300 C132 330 169 340 169 380 V1085 Q169 1100 154 1100 H15 Q0 1100 0 1085 V380 C0 340 37 330 37 300 Z" fill="url(#glass-shade)" stroke="var(--glass-edge)" stroke-width="2"/>
    <rect x="37" y="0" width="95" height="146" rx="5" fill="var(--cap)"/>
    <rect x="37" y="143" width="95" height="160" fill="var(--neck-dark)"/>
    <ellipse cx="84.5" cy="1035" rx="78" ry="18" fill="#ffffff" fill-opacity="0.2"/>
  </svg>
  <div class="neck-mark berry">Verdance</div>
  <div class="label-clear">
    <div class="tier top"></div><div class="tier mid"></div><div class="tier low"></div>
    <div class="flavor">BERRY</div>
    <svg class="fruit" role="img" aria-label="Vintage botanical illustration of berries with leaves and a blossom" viewBox="0 0 120 138">
      <rect width="120" height="138" fill="var(--berry)" opacity="0.5" rx="10"/>
    </svg>
    <div class="mark berry">Verdance</div>
    <div class="brand">VERDANCE<br>GARDEN<br>SPRITZERS</div>
  </div>
</div>

<div class="bottle" style="left:883px">
  <svg viewBox="0 0 169 1100" aria-hidden="true">
    <path d="M37 0 H132 V300 C132 330 169 340 169 380 V1085 Q169 1100 154 1100 H15 Q0 1100 0 1085 V380 C0 340 37 330 37 300 Z" fill="url(#glass-shade)" stroke="var(--glass-edge)" stroke-width="2"/>
    <rect x="37" y="0" width="95" height="146" rx="5" fill="var(--cap)"/>
    <rect x="37" y="143" width="95" height="160" fill="var(--neck-dark)"/>
    <ellipse cx="84.5" cy="1035" rx="78" ry="18" fill="#ffffff" fill-opacity="0.2"/>
  </svg>
  <div class="neck-mark">Verdance</div>
  <div class="label-clear">
    <div class="tier top"></div><div class="tier mid"></div><div class="tier low"></div>
    <div class="flavor">PEAR</div>
    <svg class="fruit" role="img" aria-label="Vintage botanical illustration of a pear with leaves" viewBox="0 0 120 138">
      <rect width="120" height="138" fill="var(--pear)" opacity="0.55" rx="10"/>
    </svg>
    <div class="mark">Verdance</div>
    <div class="brand">VERDANCE<br>GARDEN<br>SPRITZERS</div>
  </div>
</div>

</body>
</html>
```